Business Card Design for Marketing Firm

Looking for business card design for higher end marketing firm. Clean but impressionable/trendy. We are a marketing firm that represents manufacturers in the foodservice equipment and supply industry. Our customers are end users such has hotels, restaurants, country clubs, convention centers and casinos as well as distributors of restaurants supplies and equipment, and manufacturers of foodservice equipment and supplies.
Target Market(s)
Hotels, Restaurants, Supply & Equipment Distributors, Foodservice Manufacturers
Industry/Entity Type
Foodservice/Hospitality
Contact Information for Business Card
Name, Title, Contact Number, Email, Website, Social Media, Address
Requirements
Must have
- Clean & Simple but Serious and Impressionable

```html
<!DOCTYPE html>
<html lang="en">
<head>
<meta charset="utf-8">
<title>Meridian Group — Business Card</title>
<link rel="stylesheet" href="https://fonts.googleapis.com/css2?family=Cinzel:wght@500&family=Poppins:wght@400&display=swap">
<style>
  :root {
    --backdrop: #9b9b9b;
    --card-white: #ffffff;
    --navy: #00007f;
    --ink: #111111;
    --link-blue: #1a1aa6;
    --emboss: #1616b4;
    --shadow: rgba(0, 0, 0, 0.55);
  }
  * { margin: 0; padding: 0; box-sizing: border-box; }
  html, body { width: 1093px; height: 1200px; overflow: hidden; }
  body { background: var(--backdrop); position: relative; font-family: "Poppins", sans-serif; }

  .card {
    position: absolute;
    border-radius: 24px;
    overflow: hidden;
    box-shadow: 3px 4px 3px var(--shadow);
  }
  .card--front { left: 264px; top: 226px; width: 578px; height: 356px; background: var(--card-white); }
  .card--back { left: 264px; top: 621px; width: 583px; height: 357px; background: var(--navy); }

  .front__band { position: absolute; left: 0; right: 0; bottom: 0; height: 14px; background: var(--navy); }

  .holder { position: absolute; left: 37px; top: 56px; }
  .holder__name { font-family: "Cinzel", serif; font-weight: 500; font-size: 24px; color: var(--navy); line-height: 1; letter-spacing: 0.3px; }
  .holder__title { font-size: 16.5px; color: #222; line-height: 1.1; margin-top: 2px; }

  .brand { position: absolute; display: flex; flex-direction: column; align-items: center; }
  .brand__dot { border-radius: 50%; }
  .brand__name { font-family: "Cinzel", serif; font-weight: 500; line-height: 1; white-space: nowrap; }

  .card--front .brand { left: 300px; top: 40px; width: 248px; color: var(--navy); }
  .card--front .brand__dot { width: 44px; height: 44px; background: var(--navy); margin-bottom: 26px; }
  .card--front .brand__name { font-size: 27px; }

  .card--back .brand { left: 0; right: 0; top: 84px; color: var(--emboss); }
  .card--back .brand__dot { width: 60px; height: 60px; background: var(--emboss); margin-bottom: 34px; }
  .card--back .brand__name { font-size: 34px; }

  .contact { position: absolute; left: 37px; top: 251px; list-style: none; font-size: 16.5px; color: var(--ink); }
  .contact__item { display: flex; align-items: center; height: 21px; }
  .contact__icon { width: 15px; height: 15px; margin-right: 8px; fill: none; stroke: var(--navy); stroke-width: 1.8; }
  .contact__web { color: var(--link-blue); }

  .social { position: absolute; left: 450px; top: 235px; display: flex; gap: 6px; }
  .social__dot { width: 26px; height: 26px; border-radius: 50%; background: var(--navy); }

  .address { position: absolute; right: 32px; top: 272px; text-align: right; font-size: 16.5px; color: var(--ink); line-height: 21px; font-style: normal; }
</style>
</head>
<body>

<section class="card card--front">
  <div class="holder">
    <h1 class="holder__name">DANIEL HARLOW</h1>
    <p class="holder__title">Managing Director</p>
  </div>

  <div class="brand">
    <span class="brand__dot"></span>
    <span class="brand__name">MERIDIAN GROUP</span>
  </div>

  <ul class="contact">
    <li class="contact__item">
      <svg class="contact__icon" viewBox="0 0 16 16"><path d="M3 1.5l3 3-1.6 1.8c.8 2 2.3 3.5 4.3 4.3L10.5 9l3 3-2 2C6 13.5 2.5 10 2 4.5z"/></svg>
      044-555 010 273
    </li>
    <li class="contact__item">
      <svg class="contact__icon" viewBox="0 0 16 16"><rect x="1" y="3" width="14" height="10"/><path d="M1 3l7 6 7-6"/></svg>
      hello@meridiangroup.com
    </li>
    <li class="contact__item">
      <svg class="contact__icon" viewBox="0 0 16 16"><circle cx="8" cy="8" r="6.5"/><ellipse cx="8" cy="8" rx="3" ry="6.5"/><path d="M1.5 8h13M2.5 5h11M2.5 11h11"/></svg>
      www.<span class="contact__web">meridiangroup</span>.com
    </li>
  </ul>

  <div class="social" aria-label="Social media">
    <span class="social__dot"></span>
    <span class="social__dot"></span>
    <span class="social__dot"></span>
  </div>

  <address class="address">88, Harbour Street Suite<br>10234, Northland</address>

  <div class="front__band"></div>
</section>

<section class="card card--back">
  <div class="brand">
    <span class="brand__dot"></span>
    <span class="brand__name">MERIDIAN GROUP</span>
  </div>
</section>

</body>
</html>
```